Modern, clean business card for Clearbrook Optics

Updated business card with a modern look.

Logo on the front
Dr Tavin R Marquell and Associates on the front.
Three locations on the back:
Ridgefront Brantmart
509-555-0142
18342 E Fernhollow Ave

Pelham Brantmart
509-555-0187
4716 W Dunmore Ave

Copper Bluff Brantmart
509-555-0163
3854 S Kettering Rd

Friendwall icon. www.clearbrookoptix.example

Nice open white space on back for writing next appointment time.

Target Market(s)

Main target is female 25-50, but I would like broad appeal.

Industry/Entity Type

Healthcare

Contact Information for Business Card

Modern look

Font styles to use
Serif

Requirements
Must have
• Logo and Dr Tavin R Marquell and Associates on front.
• 3 locations on back
• white space for noting next appointment

```html
<!DOCTYPE html>
<html lang="en">
<head>
<meta charset="utf-8">
<title>Clearbrook Optics – Business Card</title>
<link rel="stylesheet" href="https://fonts.googleapis.com/css2?family=Open+Sans:wght@400;600;700&display=swap">
<style>
  :root {
    --bg: #e6e7e9;
    --card: #ffffff;
    --navy: #1e3f7a;
    --blue: #1a6fc0;
    --ink-grey: #6a6a6a;
    --rule: #8a8d92;
    --band-dark: #1b3a72;
    --band-light: #2d7fd0;
  }
  * { box-sizing: border-box; margin: 0; padding: 0; }
  html, body {
    width: 1105px; height: 1200px; overflow: hidden;
    background: var(--bg);
    font-family: "Open Sans", Arial, sans-serif;
  }
  .card {
    position: absolute; left: 192px; width: 720px; height: 412px;
    background: var(--card);
    box-shadow: 0 2px 8px rgba(0,0,0,0.18);
  }
  .card--front { top: 146px; }
  .card--back { top: 602px; }

  .social {
    position: absolute; top: 18px; right: 18px;
    display: flex; align-items: center; gap: 6px;
    font-size: 13px; font-weight: 600; color: var(--blue);
  }
  .social__square { width: 14px; height: 14px; background: var(--blue); }

  .brand-name {
    position: absolute; top: 196px; left: 0; width: 100%;
    text-align: center; font-size: 38px; font-weight: 700;
    color: var(--navy); letter-spacing: 0.5px;
  }
  .practice-name {
    position: absolute; top: 318px; left: 0; width: 100%;
    text-align: center; font-size: 25px; font-weight: 600; color: var(--navy);
  }

  .field {
    position: absolute; left: 41px; display: flex; align-items: flex-end;
    font-size: 19px; color: var(--navy);
  }
  .field__line { border-bottom: 1.5px solid var(--rule); height: 1px; margin-left: 18px; margin-bottom: 5px; }
  .field--name { top: 56px; }
  .field--name .field__line { width: 563px; }
  .field--date { top: 117px; }
  .field--date .field__line { width: 263px; }
  .field__time { margin-left: 18px; }
  .field--date .field__line--time { width: 150px; margin-right: 14px; }
  .field--note { top: 173px; }
  .field--note .field__line { width: 563px; }

  .location { position: absolute; top: 262px; font-size: 18px; line-height: 25px; color: var(--ink-grey); }
  .location__name { font-weight: 700; color: var(--navy); }
  .location--1 { left: 40px; }
  .location--2 { left: 253px; }
  .location--3 { left: 457px; }

  .footer-rule { position: absolute; left: 0; right: 0; top: 364px; border-top: 1.5px solid #c9ccd1; }
  .footer-band {
    position: absolute; left: 0; right: 0; bottom: 0; height: 40px;
    background: linear-gradient(90deg, var(--band-dark) 0%, var(--band-light) 55%, var(--band-dark) 100%);
    color: #fff; font-size: 18px; text-align: center; line-height: 40px;
  }
</style>
</head>
<body>
  <section class="card card--front">
    <div class="social"><span class="social__square"></span>Friendwall</div>
    <div class="brand-name">Clearbrook Optics</div>
    <div class="practice-name">Dr Tavin R Marquell &amp; Associates</div>
  </section>

  <section class="card card--back">
    <div class="field field--name">Name<span class="field__line"></span></div>
    <div class="field field--date">Date<span class="field__line"></span><span class="field__time">Time</span><span class="field__line field__line--time"></span>am/pm</div>
    <div class="field field--note">Note<span class="field__line"></span></div>

    <div class="location location--1">
      <div class="location__name">Ridgefront Brantmart</div>
      <div>509-555-0142</div>
      <div>18342 E Fernhollow Ave</div>
    </div>
    <div class="location location--2">
      <div class="location__name">Pelham Brantmart</div>
      <div>509-555-0187</div>
      <div>4716 W Dunmore Ave</div>
    </div>
    <div class="location location--3">
      <div class="location__name">Copper Bluff Brantmart</div>
      <div>509-555-0163</div>
      <div>3854 S Kettering Rd</div>
    </div>

    <div class="footer-rule"></div>
    <div class="footer-band">www.clearbrookoptix.example</div>
  </section>
</body>
</html>
```